Brell Stone Company Business Cards

Front and Back Business Card - logo and text setup - cool design. I need workable photoshop or illustrator files so I can setup each employee card with design that is created
Updates

Hi everyone, thank you for the great entries. Please no more white and blue cards - there are so many already - black and silver only now please. thanks!

Target Market(s)

Construction Industry - Facility Managers

Industry/Entity Type

Construction

Contact Information for Business Card

I really like contemporary simplistic looks - clean neat....not opposed to seeing some black backrounds

Requirements
Must have
• Logo/website address with design on front only - www.brellstone-example.com (logo attached)
• Back:
• Name/Title/Company Address/Phone/email address
Nice to have
• Cool design
Should not have
• Nothing gimmicky like Fire or Water - since we are a Fire Protection company - it has all been done

```html
<!DOCTYPE html>
<html lang="en">
<head>
<meta charset="utf-8">
<title>Brell Stone Company Business Cards</title>
<link rel="stylesheet" href="https://fonts.googleapis.com/css2?family=Arimo:wght@400;700&display=swap">
<style>
  :root {
    --card: #111214;
    --card-edge: #2e3034;
    --silver: #c5c9cf;
    --silver-bright: #eef0f3;
    --silver-dim: #8d9299;
    --backdrop: #3a3b3e;
  }
  html, body {
    margin: 0;
    padding: 0;
    width: 1200px;
    height: 880px;
    overflow: hidden;
    background: var(--backdrop);
    font-family: "Arimo", Arial, sans-serif;
  }
  .sheet {
    position: relative;
    width: 1200px;
    height: 880px;
  }
  .card {
    position: absolute;
    left: 250px;
    width: 700px;
    height: 400px;
    background: var(--card);
    border: 1px solid var(--card-edge);
    box-sizing: border-box;
    border-radius: 24px;
    box-shadow: 0 10px 30px rgba(0,0,0,0.5);
    overflow: hidden;
  }
  .card--front { top: 24px; }
  .card--back { top: 456px; }

  /* Front */
  .brand {
    position: absolute;
    left: 0;
    right: 0;
    top: 150px;
    display: flex;
    justify-content: center;
    align-items: center;
    gap: 14px;
  }
  .brand__mark {
    width: 22px;
    height: 22px;
    background: var(--silver-dim);
  }
  .brand__name {
    font-weight: 700;
    font-size: 58px;
    letter-spacing: -1px;
    color: var(--silver-bright);
  }
  .brand__web {
    position: absolute;
    left: 0;
    right: 0;
    top: 252px;
    text-align: center;
    font-weight: 700;
    font-size: 15px;
    letter-spacing: 6px;
    color: var(--silver);
  }

  /* Back */
  .person {
    position: absolute;
    right: 410px;
    top: 58px;
    text-align: right;
  }
  .person__name {
    font-weight: 700;
    font-size: 26px;
    color: var(--silver-bright);
    line-height: 1;
  }
  .person__title {
    font-size: 16px;
    color: var(--silver-dim);
    margin-top: 2px;
  }
  .divider {
    position: absolute;
    left: 305px;
    top: 40px;
    width: 2px;
    height: 230px;
    background: var(--silver-dim);
  }
  .contact {
    position: absolute;
    left: 340px;
    top: 158px;
    font-size: 15px;
    line-height: 20px;
    color: var(--silver);
  }
  .contact__row {
    display: flex;
    align-items: center;
    gap: 10px;
  }
  .contact__row svg {
    width: 14px;
    height: 14px;
    flex: none;
  }
  .contact__address { margin-bottom: 4px; }
  .contact__web-domain { color: var(--silver-bright); }
</style>
</head>
<body>
<main class="sheet">
  <section class="card card--front" aria-label="Card front">
    <div class="brand">
      <span class="brand__mark"></span>
      <span class="brand__name">Brell Stone</span>
    </div>
    <div class="brand__web">www.brellstone-example.com</div>
  </section>

  <section class="card card--back" aria-label="Card back">
    <div class="person">
      <div class="person__name">Dana Whitlow</div>
      <div class="person__title">Director</div>
    </div>
    <div class="divider"></div>
    <div class="contact">
      <div class="contact__address">PO Box 480, Harbor Lane<br>4th Street, Kestrel Bay</div>
      <div class="contact__row">
        <svg viewBox="0 0 14 14" aria-hidden="true"><rect x="3" y="1" width="8" height="12" rx="1.5" fill="none" stroke="#8d9299" stroke-width="1.6"/></svg>
        <span>(555) 014 2290</span>
      </div>
      <div class="contact__row">
        <svg viewBox="0 0 14 14" aria-hidden="true"><rect x="1" y="3" width="12" height="8" fill="#8d9299"/><path d="M1 3 L7 8 L13 3" fill="none" stroke="#111214" stroke-width="1.2"/></svg>
        <span>info@brellstone-example.com</span>
      </div>
      <div class="contact__row">
        <svg viewBox="0 0 14 14" aria-hidden="true"><circle cx="7" cy="7" r="5.5" fill="none" stroke="#8d9299" stroke-width="1.4"/><ellipse cx="7" cy="7" rx="2.4" ry="5.5" fill="none" stroke="#8d9299" stroke-width="1"/><path d="M1.5 7 H12.5" stroke="#8d9299" stroke-width="1"/></svg>
        <span>www.<span class="contact__web-domain">brellstone-example</span>.com</span>
      </div>
    </div>
  </section>
</main>
</body>
</html>
```